Landing Page and Logo for Auto-Blogging Platform

I created a platform that allows users to start a blog for their business, hobby, charity, etc. I need a landing page where users can learn about the platform, benefits of consistent blogging, SEO value, plans/pricing, etc. The landing page needs to have multiple call to action buttons encouraging the visitor to register/sign up for a free trial.

In addition to the landing page, I need a page for users to establish the settings for their blog. This page should be a fairly simple form, intended for the user to enter a few details to set up their blog:
1. Name of Blog
2. Up to 10 topics and/or keywords the blog should focus on
3. Theme: Color-scheme and logo upload for blog.

I have attached the specifications of the platform's functionality so you can better understand how it works, plans/pricing, etc.

I also need a logo for the business. The name of the platform is PostNook.

Target Market(s)

Website owners, bloggers, business owners

Industry/Entity Type

Technology, Internet, web design

Coding

Coded - Design and coding required

Number of Pages Required

2 page

Colors
0054AA
0677BA
7BADD7
CADEEF
E8F1F8
0094D4
00A9DD
6FCCEA
C7EBF8
E9F6FB

Requirements
Must have
• Eye-catching design but fairly light on content (keep it simple and brief.)
Nice to have
• Eye-catching yet simple design, clean and easy to understand what we are offering.
Should not have
• Too much “wordy” and confusing content.

```html
<!DOCTYPE html>
<html lang="en">
<head>
<meta charset="utf-8">
<title>PostNook – Automate Your Blog Posting with AI</title>
<link rel="stylesheet" href="https://fonts.googleapis.com/css2?family=Montserrat:wght@600;700;800&family=Poppins:wght@400;500;600;700&display=swap">
<style>
:root{
  --blue-deep:#0054AA;
  --blue:#0677BA;
  --blue-bright:#0094D4;
  --cyan:#00A9DD;
  --sky:#7BADD7;
  --pale:#E8F1F8;
  --ice:#E9F6FB;
  --ink:#111418;
  --text:#3c4350;
  --muted:#6b7280;
  --white:#ffffff;
  --footer:#0d0d0f;
}
*{margin:0;padding:0;box-sizing:border-box}
html,body{width:1200px;height:4173px;overflow:hidden}
body{position:relative;background:var(--white);font-family:"Poppins",sans-serif;color:var(--text)}
.abs{position:absolute}
.heading{font-family:"Montserrat",sans-serif;font-weight:800;text-transform:uppercase;letter-spacing:.3px}
.accent{color:var(--blue-bright)}
.btn{position:absolute;display:flex;align-items:center;justify-content:center;border-radius:30px;
  background:linear-gradient(90deg,var(--cyan),var(--blue-deep));color:var(--white);font-weight:600;font-size:15px}
.swoosh{position:absolute;left:50%;transform:translateX(-50%)}

/* header */
.top-rule{top:0;left:0;width:1200px;height:4px;background:var(--blue-deep)}
.brand{display:flex;align-items:center;gap:10px;font-family:"Montserrat",sans-serif;font-weight:800;font-size:30px}
.brand-dot{width:26px;height:26px;border-radius:50%;background:var(--blue-bright)}
.header-brand{top:28px;left:110px;color:var(--ink)}
.nav{top:36px;left:0;width:1200px;font-size:16px;color:var(--muted)}
.nav span{position:absolute;top:0}
.nav .active{color:var(--blue)}
.nav-underline{position:absolute;top:26px;left:449px}
.contact-btn{top:24px;left:954px;width:134px;height:44px;font-size:16px}

/* hero */
.hero{top:94px;left:0;width:1200px;height:502px;
  background:linear-gradient(100deg,#dfe8f1 0%,#e3ecf4 40%,#c9d8e6 60%,#8aa9c6 100%)}
.hero-photo{top:94px;left:560px;width:640px;height:502px;
  background:linear-gradient(105deg,rgba(220,230,240,0) 0%,#a9c1d8 30%,#5f7f9f 65%,#3c5673 100%)}
.hero-title{top:160px;left:74px;font-size:45px;line-height:63px;color:var(--blue)}
.hero-copy{top:294px;left:74px;width:500px;font-size:16px;line-height:31px;color:var(--ink);font-weight:500}
.hero-btn{top:474px;left:74px;width:150px;height:44px}
.scroll-tab{top:570px;left:570px}

/* methods */
.section-title{left:0;width:1200px;text-align:center;font-size:33px;color:var(--ink)}
.section-lead{left:0;width:1200px;text-align:center;font-size:16px;line-height:34px;color:var(--muted)}
.method-photo{width:424px;height:284px;border-radius:20px}
.step-num{width:42px;height:42px;border-radius:50%;background:var(--blue-bright);color:var(--white);
  font-weight:600;font-size:16px;display:flex;align-items:center;justify-content:center;box-shadow:0 0 0 6px #e3f2fb}
.method-title{font-size:19px;line-height:34px;color:var(--ink);font-weight:500}
.method-copy{font-size:13.5px;line-height:28px;color:var(--muted)}
.right-align{text-align:right}

/* plans */
.plans{top:1941px;left:0;width:1200px;height:614px;
  background:linear-gradient(120deg,#0a4fa8 0%,#0660c4 45%,#0a55b4 100%)}
.plan{top:2117px;width:310px;height:362px;border-radius:20px;border:1.5px solid rgba(255,255,255,.25);text-align:center}
.plan-alt{background:var(--white);border:none;top:2117px;height:362px}
.plan-name{position:absolute;top:30px;left:0;width:100%;font-size:29px;color:var(--white)}
.plan-alt .plan-name{color:var(--blue-deep)}
.plan-band{position:absolute;top:81px;left:0;width:100%;height:59px;background:var(--white);
  color:var(--blue-deep);font-weight:600;font-size:16.5px;display:flex;align-items:center;justify-content:center}
.plan-alt .plan-band{background:var(--blue-deep);color:var(--white)}
.plan-price{position:absolute;top:162px;left:0;width:100%;color:var(--white);font-weight:700;font-size:31px}
.plan-price small{font-size:13px;font-weight:700}
.plan-alt .plan-price{color:var(--blue-deep)}
.plan-copy{position:absolute;top:220px;left:30px;width:250px;font-size:13.5px;line-height:26px;color:var(--white)}
.plan-alt .plan-copy{color:var(--muted)}
.plan-btn{top:290px;left:88px;width:134px;height:36px;font-size:15px;background:var(--cyan)}

/* about */
.about-disc{top:2686px;left:115px;width:444px;height:444px;border-radius:50%;
  background:linear-gradient(180deg,var(--blue-bright),var(--blue-deep))}
.about-device{top:2749px;left:89px;width:494px;height:318px;border-radius:14px 14px 6px 6px;
  background:linear-gradient(180deg,#2a2d33 0%,#eef3f9 6%,#dfe8f3 90%,#c7ccd2 100%);box-shadow:0 10px 20px rgba(0,0,0,.2)}
.about-title{top:2676px;left:651px;font-size:33px;color:var(--ink)}
.about-copy{top:2779px;left:637px;width:470px;font-size:16px;line-height:33.5px;color:var(--text)}
.about-copy p+p{margin-top:14px}
.about-btn{top:3089px;left:637px;width:145px;height:42px}

/* setup */
.setup-card{width:232px;height:318px;background:var(--white);border-radius:14px;
  box-shadow:0 6px 28px rgba(20,40,80,.09);text-align:center}
.setup-icon{position:absolute;top:29px;left:69px;width:94px;height:94px;border-radius:50%;
  background:linear-gradient(180deg,var(--blue-bright),var(--blue-deep));display:flex;align-items:center;justify-content:center}
.setup-step{position:absolute;top:152px;left:0;width:100%;font-weight:500;font-size:19px;color:var(--ink)}
.setup-copy{position:absolute;top:194px;left:26px;width:180px;font-size:15px;line-height:27px;color:var(--muted)}

/* footer */
.footer{top:3875px;left:0;width:1200px;height:298px;background:var(--footer)}
.footer-brand{top:3952px;left:0;width:1200px;justify-content:center;color:var(--white);font-size:38px}
.footer-nav span{position:absolute;top:4030px;color:var(--white);font-size:16px;font-weight:500}
.social{top:4079px;width:38px;height:38px;border-radius:50%;background:var(--blue-deep)}
.copyright{top:4138px;left:0;width:1200px;text-align:center;color:var(--white);font-size:12px}
</style>
</head>
<body>

<!-- Header -->
<div class="abs top-rule"></div>
<div class="abs brand header-brand"><span class="brand-dot"></span>PostNook</div>
<nav class="abs nav">
  <span class="active" style="left:449px">Home</span>
  <span style="left:541px">About Us</span>
  <span style="left:655px">Services</span>
  <span style="left:763px">Reviews</span>
  <span style="left:870px">Blogs</span>
</nav>
<svg class="nav-underline abs" style="top:60px;left:449px" width="48" height="6"><path d="M2 4 Q24 -1 46 3" stroke="#0677BA" stroke-width="2" fill="none"/></svg>
<div class="btn contact-btn">Contact Us</div>

<!-- Hero -->
<section>
  <div class="abs hero"></div>
  <div class="abs hero-photo" role="img" aria-label="Photo of a man typing at a computer with data dashboards on screen"></div>
  <h1 class="abs heading hero-title">Automate your blog<br>posting with AI</h1>
  <p class="abs hero-copy">Transform your blogging experience with our AI-powered platform that not only generates and optimizes content tailored to your audience but also continuously learns and adapts to deliver smarter insights, ensuring your voice stands out in a crowded digital landscape.</p>
  <div class="btn hero-btn">Get Started</div>
  <svg class="abs scroll-tab" width="60" height="30" viewBox="0 0 60 30"><path d="M0 30 Q30 -6 60 30Z" fill="#fff"/><rect x="22" y="6" width="16" height="24" rx="8" fill="#8a929c"/><path d="M30 11 V24 M25 20 L30 25 L35 20" stroke="#fff" stroke-width="2" fill="none"/></svg>
</section>

<!-- Methods -->
<section>
  <h2 class="abs heading section-title" style="top:686px">Methods to create <span class="accent">blog topics</span></h2>
  <svg class="swoosh" style="top:744px" width="120" height="18"><path d="M2 16 Q60 0 118 4 Q60 6 2 16Z" fill="#111"/></svg>
  <p class="abs section-lead" style="top:786px">Denounce with righteous indignation and dislike men who are so beguiled and demoralized by the charms of<br>pleasure of the moment, so blinded by desire, that they cannot foresee the pain and trouble</p>

  <svg class="abs" style="top:1060px;left:550px" width="110" height="650"><path d="M96 0 V147 H12 V307 M12 307 V463 H96 V631" stroke="#0677BA" stroke-width="2.5" stroke-dasharray="3 4" fill="none"/></svg>

  <div class="abs method-photo" style="top:902px;left:180px;background:linear-gradient(135deg,#a9c6df,#5b8fc0 55%,#24406e)" role="img" aria-label="Photo of a hand touching floating digital content panels"></div>
  <div class="abs step-num" style="top:1035px;left:625px">01</div>
  <h3 class="abs method-title" style="top:963px;left:697px;width:360px">The user enters them into a table manually</h3>
  <p class="abs method-copy" style="top:1039px;left:697px;width:370px">Lorem ipsum dolor sit amet, consectetur adipiscing elit, sed do eiusmod tempor incididunt ut labore et dolore magna aliqua.</p>

  <div class="abs method-photo" style="top:1234px;left:596px;background:linear-gradient(135deg,#16294d,#3e6ea8 50%,#c6d9ee)" role="img" aria-label="Photo of hands holding a tablet with a wall of video thumbnails"></div>
  <div class="abs step-num" style="top:1346px;left:541px">02</div>
  <h3 class="abs method-title right-align" style="top:1287px;left:136px;width:360px">The user uploads a list of blog topics in CSV format.</h3>
  <p class="abs method-copy right-align" style="top:1363px;left:136px;width:360px">Lorem ipsum dolor sit amet, consectetur adipiscing elit, sed do eiusmod tempor incididunt ut labore et dolore magna aliqua. Ut enim ad</p>

  <div class="abs method-photo" style="top:1550px;left:180px;background:radial-gradient(circle at 45% 40%,#6fb8ea,#1a4fa3 45%,#0b2a66)" role="img" aria-label="Illustration of a robot hand holding a globe of media panels with binary code"></div>
  <div class="abs step-num" style="top:1670px;left:625px">03</div>
  <h3 class="abs method-title" style="top:1613px;left:697px;width:400px">AI can create the list of blog topics based on a prompt</h3>
  <p class="abs method-copy" style="top:1687px;left:697px;width:330px">"Provide a list of 52 blog topics for a handyman business's blog</p>
</section>

<!-- Plans -->
<section>
  <div class="abs plans" role="img" aria-label="Blue tinted collage of business and technology photos"></div>
  <h2 class="abs heading section-title" style="top:2009px;color:var(--white)">Our subscriptions plan</h2>
  <svg class="swoosh" style="top:2066px" width="120" height="18"><path d="M2 16 Q60 0 118 4 Q60 6 2 16Z" fill="#fff"/></svg>

  <div class="abs plan" style="left:112px">
    <div class="heading plan-name">Base Plan</div>
    <div class="plan-band">1 Blog Post (up to 2,000 words)</div>
    <div class="plan-price">$9.99<small>/mo. Every Month</small></div>
    <p class="plan-copy">Exercitation ullamco laboris nisi ut ali quip ex ea commodo cons</p>
    <div class="btn plan-btn">Choose Plan</div>
  </div>
  <div class="abs plan plan-alt" style="left:445px">
    <div class="heading plan-name">Premium Plan</div>
    <div class="plan-band">1 Blog Post (up to 2,000 words)</div>
    <div class="plan-price">$14.99<small>/mo. Every Week</small></div>
    <p class="plan-copy">Exercitation ullamco laboris nisi ut ali quip ex ea commodo cons</p>
    <div class="btn plan-btn">Choose Plan</div>
  </div>
  <div class="abs plan" style="left:779px">
    <div class="heading plan-name">Ultimate Plan</div>
    <div class="plan-band">1 Blog Post (up to 3,000 words)</div>
    <div class="plan-price">$24.99<small>/mo. Every Day</small></div>
    <p class="plan-copy">Exercitation ullamco laboris nisi ut ali quip ex ea commodo cons</p>
    <div class="btn plan-btn">Choose Plan</div>
  </div>
</section>

<!-- About -->
<section>
  <div class="abs about-disc"></div>
  <div class="abs about-device" role="img" aria-label="Laptop showing the PostNook analytics dashboard"></div>
  <h2 class="abs heading about-title">About <span class="accent">us</span></h2>
  <svg class="abs" style="top:2728px;left:651px" width="120" height="18"><path d="M2 16 Q60 0 118 4 Q60 6 2 16Z" fill="#111"/></svg>
  <div class="abs about-copy">
    <p>The purpose of this platform is to allow anyone to start a blog and automate the process of creating content and posting it to the blog.</p>
    <p>Each user will have a dashboard where they control their settings such as account information, billing, view blog posts, view blog post topics, etc. From this dashboard, the user can customize the “look and feel” of their blog including theme, hero banner, header, footer, logo, color scheme, etc.</p>
  </div>
  <div class="btn about-btn">Read More</div>
</section>

<!-- Setup steps -->
<section>
  <h2 class="abs heading section-title" style="top:3257px">How to set up <span class="accent">the auto-blog</span></h2>
  <svg class="swoosh" style="top:3314px" width="120" height="18"><path d="M2 16 Q60 0 118 4 Q60 6 2 16Z" fill="#111"/></svg>
  <p class="abs section-lead" style="top:3353px">Denounce with righteous indignation and dislike men who are so beguiled and demoralized</p>

  <div class="abs setup-card" style="top:3428px;left:99px">
    <div class="setup-icon"><svg width="46" height="46" viewBox="0 0 46 46" fill="none" stroke="#fff" stroke-width="2.5"><circle cx="15" cy="15" r="9"/><circle cx="31" cy="31" r="9"/><path d="M15 10v5h4M31 26v5h4"/></svg></div>
    <div class="setup-step">STEP 1</div>
    <p class="setup-copy">Select frequency of Automated Blog Posts (daily, weekly, or monthly)</p>
  </div>
  <div class="abs setup-card" style="top:3460px;left:355px">
    <div class="setup-icon"><svg width="46" height="46" viewBox="0 0 46 46" fill="none" stroke="#fff" stroke-width="2.5"><rect x="6" y="10" width="26" height="26" rx="3"/><path d="M20 26l16-16 4 4-16 16h-4z"/></svg></div>
    <div class="setup-step">STEP 2</div>
    <p class="setup-copy">Name your blog</p>
  </div>
  <div class="abs setup-card" style="top:3428px;left:612px">
    <div class="setup-icon"><svg width="46" height="46" viewBox="0 0 46 46" fill="none" stroke="#fff" stroke-width="2.5"><rect x="6" y="6" width="34" height="34" rx="3"/><path d="M6 14h34M12 22h22M12 28h22M12 34h14"/></svg></div>
    <div class="setup-step">STEP 3</div>
    <p class="setup-copy">Select your blog topics (or let AI choose them for you)</p>
  </div>
  <div class="abs setup-card" style="top:3460px;left:868px">
    <div class="setup-icon"><svg width="46" height="46" viewBox="0 0 46 46" fill="none" stroke="#fff" stroke-width="2.5"><rect x="5" y="7" width="36" height="24" rx="2"/><path d="M17 39h12M23 31v8M14 24l12-12 3 3-12 12h-3z"/></svg></div>
    <div class="setup-step">STEP 4</div>
    <p class="setup-copy">Go do something else and let AI do all your blogging for you!</p>
  </div>
</section>

<!-- Footer -->
<footer>
  <div class="abs footer"></div>
  <div class="abs brand footer-brand"><span class="brand-dot"></span>PostNook</div>
  <div class="footer-nav">
    <span style="left:243px">Home</span>
    <span style="left:358px">About Us</span>
    <span style="left:496px">Services</span>
    <span style="left:628px">Reviews</span>
    <span style="left:759px">Blogs</span>
    <span style="left:870px">Contact Us</span>
  </div>
  <div class="abs social" style="left:480px"></div>
  <div class="abs social" style="left:531px"></div>
  <div class="abs social" style="left:581px"></div>
  <div class="abs social" style="left:631px"></div>
  <div class="abs social" style="left:681px"></div>
  <p class="abs copyright">(C) Copyright 2024 | All Rights Reserved</p>
</footer>

</body>
</html>
```